We are a building company that build new homes and units we are looking for something fresh and looks good my company name is
Lark Building Co Pty Ltd

Industry/Entity Type

Building

Contact Information for Business Card

Name Marco Ellis-Dunford
Tittle: Director
Address 14 Corrin St. Pelham Vale Vic 3179
Ph: 03 9582 4063
Mobile : 0400 362 918

www.larkbuildingco.com.au
Email: sales@larkbuildingco.com.au

```html
<!DOCTYPE html>
<html lang="en">
<head>
<meta charset="utf-8">
<title>Lark Building Co – Business Card</title>
<link rel="stylesheet" href="https://fonts.googleapis.com/css2?family=Saira+Semi+Condensed:wght@400;600&family=Saira:wght@500&family=Handlee&display=swap">
<style>
  :root {
    --navy: #263c8e;
    --sky: #00a7e6;
    --white: #ffffff;
    --rule: rgba(255,255,255,0.85);
    --page: #ffffff;
  }
  html, body {
    margin: 0;
    width: 1200px;
    height: 693px;
    overflow: hidden;
    background: var(--page);
  }
  .canvas {
    position: relative;
    width: 1200px;
    height: 693px;
  }
  .card {
    position: absolute;
    overflow: hidden;
    box-shadow: 0 2px 10px rgba(0,0,0,0.35);
  }

  /* Front */
  .card-front {
    left: 94px; top: 53px;
    width: 361px; height: 586px;
    background: var(--white);
  }
  .brand {
    position: absolute;
    left: 0; right: 0; top: 150px;
    display: flex; flex-direction: column; align-items: center;
  }
  .brand-square {
    width: 46px; height: 46px;
    background: var(--sky);
    margin-bottom: 34px;
  }
  .brand-name {
    margin: 0;
    font-family: "Saira", sans-serif;
    font-weight: 500;
    font-size: 31px;
    line-height: 1.15;
    letter-spacing: 3px;
    color: var(--navy);
    text-align: center;
  }
  .front-band {
    position: absolute;
    left: 0; right: 0; bottom: 0;
    height: 76px;
    background: var(--navy);
    display: flex; align-items: center; justify-content: center;
  }
  .front-tagline {
    margin: 0 0 8px;
    font-family: "Handlee", cursive;
    font-size: 17px;
    color: var(--white);
  }

  /* Back */
  .card-back {
    left: 498px; top: 179px;
    width: 613px; height: 360px;
    background: var(--navy);
  }
  .accent-strip {
    position: absolute; left: 0; top: 0;
  }
  .strip-shade {
    position: absolute; left: 108px; top: 0;
    width: 14px; height: 360px;
    background: linear-gradient(to right, rgba(0,0,0,0.35), rgba(0,0,0,0));
  }
  .person-name {
    position: absolute;
    left: 155px; top: 46px;
    margin: 0;
    font-family: "Saira Semi Condensed", sans-serif;
    font-weight: 600;
    font-size: 31px;
    letter-spacing: 0.5px;
    color: var(--white);
  }
  .name-rule {
    position: absolute;
    left: 155px; top: 92px;
    width: 445px; height: 2px;
    background: linear-gradient(to right, var(--rule), rgba(255,255,255,0));
  }
  .contact-list {
    position: absolute;
    left: 155px; top: 0;
    margin: 0; padding: 0; list-style: none;
  }
  .contact-item {
    position: absolute;
    left: 0;
    display: flex; align-items: center;
    white-space: nowrap;
    font-family: "Saira Semi Condensed", sans-serif;
    font-size: 24px;
    color: var(--white);
  }
  .contact-item svg { width: 26px; height: 26px; margin-right: 14px; }
  .contact-phone  { top: 101px; }
  .contact-mobile { top: 136px; }
  .contact-web    { top: 183px; }
  .contact-email  { top: 215px; }
  .back-tagline {
    position: absolute;
    left: 152px; top: 298px;
    margin: 0;
    font-family: "Handlee", cursive;
    font-size: 22px;
    color: var(--white);
  }
</style>
</head>
<body>
<main class="canvas">

  <section class="card card-front" aria-label="Card front">
    <div class="brand">
      <div class="brand-square"></div>
      <h1 class="brand-name">LARK BUILDING<br>CO</h1>
    </div>
    <div class="front-band">
      <p class="front-tagline">New home design and construction</p>
    </div>
  </section>

  <section class="card card-back" aria-label="Card back">
    <svg class="accent-strip" width="108" height="360" viewBox="0 0 108 360">
      <rect width="108" height="360" fill="var(--sky)"/>
      <polygon points="0,360 108,360 108,284" fill="var(--white)"/>
    </svg>
    <div class="strip-shade"></div>

    <h2 class="person-name">MARCO ELLIS-DUNFORD</h2>
    <div class="name-rule"></div>

    <ul class="contact-list">
      <li class="contact-item contact-phone">
        <svg viewBox="0 0 24 24" fill="none" stroke="#fff" stroke-width="1.6" stroke-linejoin="round"><path d="M6 3l3 4-2 2c1 3 4 6 7 7l2-2 4 3-2 3c-7 0-15-8-15-15z"/></svg>
        03 9582 4063
      </li>
      <li class="contact-item contact-mobile">
        <svg viewBox="0 0 24 24" fill="none" stroke="#fff" stroke-width="1.6"><rect x="6" y="2" width="12" height="20" rx="2"/><rect x="8.5" y="5" width="7" height="11" fill="#fff" stroke="none"/><circle cx="12" cy="19" r="0.9" fill="#fff"/></svg>
        0400 362 918
      </li>
      <li class="contact-item contact-web">
        <svg viewBox="0 0 24 24" fill="none" stroke="#fff" stroke-width="1.6"><rect x="4" y="5" width="16" height="11"/><path d="M2 19h20"/></svg>
        www.larkbuildingco.com.au
      </li>
      <li class="contact-item contact-email">
        <svg viewBox="0 0 24 24" fill="none" stroke="#fff" stroke-width="1.6" stroke-linejoin="round"><rect x="3" y="6" width="18" height="12"/><path d="M3 6l9 7 9-7M3 18l7-6M21 18l-7-6"/></svg>
        sales@larkbuildingco.com.au
      </li>
    </ul>

    <p class="back-tagline">Quality, excellence and innovation</p>
  </section>

</main>
</body>
</html>
```